Plakat für Tanzschule
Zielgruppe
Wir sind eine Tanzschule
Hallo,
ich benötige ein professionelles Design für ein Schild im Format 2 Meter breit × 1 Meter hoch (Querformat), das von einem stark frequentierten Parkplatz aus gut sichtbar ist.
✅ Ziel:
Gestaltung eines aufmerksamkeitsstarken, eleganten und energiegeladenen Werbeschilds
Das Schild soll sofort zeigen, worum es geht (Tanzstile) und zum kostenlosen Schnuppern motivieren
Die Gestaltung soll hochwertig und grafisch modern wirken
Bild / Hintergrund:
Ich habe einen ersten Design-Vorschlag hochgeladen (Screenshot)
⚠️ Ursprünglich hatte ich vor, ein bereits ausgeschnittenes und bearbeitetes Bild zu liefern (z. B. Unreinheiten und Störungen im Bild zu glätten oder zu entfernt und Zähne etwas weißer). Das kann ich jetzt leider doch nicht nachreichen. Daher müsste doch die Bearbeitung des Bildes mit übernommen werden.
✏️ Textinhalte (hierarchisch sortiert):
TANZSCHULE
Salsa · Bachata · Kizomba · Zouk
Jetzt Gratis Schnuppern!
Ritmo del Faro (Markenname)
www.ritmo-del-faro.de
???? Wichtig:
Die wichtigsten Inhalte (Tanzarten & CTA) müssen sofort erfassbar sein
Design bitte auf Fernwirkung, klare Lesbarkeit und modernes visuelles Layout ausrichten
Text in sinnvollen Größenabstufungen und mit sauberer visueller Hierarchie
Unsere eigentliche Hauptfarbe ist #ad194f, bis jetzt habe ich aber noch keine schöne Möglichkeit gefunden, in das aktuelle Design einzuarbeiten.
????️ Endformat & Übergabe:
Bitte das fertige Layout als .afdesign Datei (Affinity Designer) liefern
Optional PSD, EPS

```html
<!DOCTYPE html>
<html lang="de">
<head>
<meta charset="utf-8">
<title>Tanzschule Ritmo del Faro – Banner</title>
<link href="https://fonts.googleapis.com/css2?family=Bebas+Neue&family=Open+Sans:wght@300;400;600;700;800&display=swap" rel="stylesheet">
<style>
  :root {
    --page: #f1f1f1;
    --banner-dark: #403d3b;
    --band-dark: #33302e;
    --swoosh: #55514e;
    --light-curve: #ecebeb;
    --text-light: #f4f3f2;
    --brand: #ad194f;
    --brand-deep: #7e0f3a;
    --brand-bright: #c92b66;
    --photo-hair: #c9a46e;
    --photo-skin: #d9a888;
    --photo-top: #e4dedb;
    --photo-shirt: #65806c;
    --photo-shirt-deep: #3f5546;
  }
  * { box-sizing: border-box; margin: 0; padding: 0; }
  html, body { width: 800px; height: 1200px; overflow: hidden; }
  body {
    background: var(--page);
    font-family: "Open Sans", sans-serif;
    position: relative;
  }
  .banner {
    position: absolute;
    left: 20px;
    width: 760px;
    height: 380px;
    background: var(--banner-dark);
    overflow: hidden;
    box-shadow: 0 18px 30px -18px rgba(0,0,0,0.35);
  }
  .banner--first { top: 170px; }
  .banner--second { top: 650px; }
  .banner__shapes { position: absolute; inset: 0; width: 760px; height: 380px; }
  .banner__photo {
    position: absolute;
    left: 0; top: 14px;
    width: 384px; height: 366px;
    border-radius: 30% 44% 0 0 / 22% 36% 0 0;
    background:
      radial-gradient(ellipse 90px 110px at 70px 110px, rgba(201,164,110,0.95), rgba(201,164,110,0) 100%),
      radial-gradient(ellipse 70px 80px at 145px 150px, rgba(217,168,136,0.9), rgba(217,168,136,0) 100%),
      radial-gradient(ellipse 70px 95px at 150px 250px, rgba(228,222,219,0.95), rgba(228,222,219,0) 100%),
      radial-gradient(ellipse 60px 60px at 260px 90px, rgba(217,168,136,0.85), rgba(217,168,136,0) 100%),
      radial-gradient(ellipse 130px 170px at 300px 240px, rgba(101,128,108,0.95), rgba(101,128,108,0) 100%),
      radial-gradient(ellipse 110px 70px at 200px 350px, rgba(63,85,70,0.9), rgba(63,85,70,0) 100%),
      linear-gradient(160deg, #7c6c5c 0%, #5e6457 55%, #45524a 100%);
    box-shadow: inset 0 0 40px rgba(0,0,0,0.25);
  }
  .brand {
    position: absolute;
    left: 452px; top: 36px;
    width: 230px;
    display: flex; align-items: center; gap: 10px;
  }
  .brand__text { display: flex; flex-direction: column; align-items: center; }
  .brand__name { font-size: 21px; font-weight: 300; color: var(--text-light); letter-spacing: 0.5px; line-height: 1.1; }
  .brand__styles { font-size: 8px; font-weight: 300; color: #cfcac6; letter-spacing: 0.3px; margin-top: 3px; }
  .brand__dot { width: 18px; height: 18px; border-radius: 50%; background: var(--brand); flex: none; }
  .headline {
    position: absolute;
    left: 396px; top: 90px;
    width: 340px;
    font-family: "Bebas Neue", sans-serif;
    font-weight: 400;
    font-size: 84px;
    line-height: 1;
    color: var(--text-light);
    text-align: center;
    letter-spacing: 1px;
  }
  .styles {
    position: absolute;
    left: 396px; top: 200px;
    width: 340px;
    font-family: "Bebas Neue", sans-serif;
    font-size: 54px;
    line-height: 44px;
    color: var(--text-light);
    text-align: center;
    letter-spacing: 1.5px;
  }
  .web {
    position: absolute;
    left: 438px; top: 332px;
    width: 252px; height: 28px;
    border-radius: 14px;
    background: linear-gradient(180deg, var(--brand-bright), var(--brand));
    display: flex; align-items: center; justify-content: center; gap: 7px;
    color: #fff;
    font-size: 14px;
  }
  .web__icon { width: 14px; height: 14px; }
  .offer {
    position: absolute;
    left: 258px; top: 220px;
    width: 140px; height: 140px;
    border-radius: 50%;
    background: radial-gradient(circle at 45% 30%, var(--brand-bright) 0%, var(--brand) 45%, var(--brand-deep) 100%);
    box-shadow: 0 4px 10px rgba(0,0,0,0.35);
    display: flex; flex-direction: column; align-items: center; justify-content: center;
    color: #fff;
    text-align: center;
    transform: rotate(-8deg);
  }
  .offer--ringed { border: 4px solid #f3f1ef; }
  .offer__lead { font-size: 15px; font-weight: 600; line-height: 1.1; }
  .offer__main { font-size: 28px; font-weight: 800; line-height: 1; letter-spacing: 0.5px; }
  .offer__tail { font-size: 15px; font-weight: 600; line-height: 1.2; }
</style>
</head>
<body>

  <section class="banner banner--first">
    <svg class="banner__shapes" viewBox="0 0 760 380" aria-hidden="true">
      <path d="M150 60 C 260 10, 400 20, 390 70 C 380 120, 300 140, 300 230 L 300 380 L 0 380 L 0 300 C 40 200, 60 110, 150 60 Z" fill="var(--swoosh)"/>
      <path d="M385 190 C 500 172, 650 170, 760 178 L 760 380 L 385 380 Z" fill="var(--band-dark)"/>
      <path d="M400 380 C 500 320, 640 304, 760 310 L 760 380 Z" fill="var(--light-curve)"/>
    </svg>
    <div class="banner__photo" role="img" aria-label="Foto eines lachenden Tanzpaares in Salsa-Haltung, Frau mit fliegenden blonden Haaren und weißem Top, Mann in grünem T-Shirt"></div>
    <div class="brand">
      <div class="brand__text">
        <span class="brand__name">Ritmo del Faro</span>
        <span class="brand__styles">Salsa · Bachata · Kizomba</span>
      </div>
      <span class="brand__dot"></span>
    </div>
    <h1 class="headline">Tanzschule</h1>
    <p class="styles">Salsa · Bachata<br>Kizomba · Zouk</p>
    <div class="offer">
      <span class="offer__lead">Jetzt</span>
      <span class="offer__main">GRATIS</span>
      <span class="offer__tail">Schnuppern!</span>
    </div>
    <div class="web">
      <svg class="web__icon" viewBox="0 0 16 16" aria-hidden="true" fill="none" stroke="#fff" stroke-width="1.4">
        <circle cx="8" cy="8" r="6.5"/><ellipse cx="8" cy="8" rx="3" ry="6.5"/><line x1="1.5" y1="8" x2="14.5" y2="8"/>
      </svg>
      <span>www.ritmo-del-faro.de</span>
    </div>
  </section>

  <section class="banner banner--second">
    <svg class="banner__shapes" viewBox="0 0 760 380" aria-hidden="true">
      <path d="M150 60 C 260 10, 400 20, 390 70 C 380 120, 300 140, 300 230 L 300 380 L 0 380 L 0 300 C 40 200, 60 110, 150 60 Z" fill="var(--swoosh)"/>
      <path d="M385 190 C 500 172, 650 170, 760 178 L 760 380 L 385 380 Z" fill="var(--band-dark)"/>
      <path d="M400 380 C 500 320, 640 304, 760 310 L 760 380 Z" fill="var(--light-curve)"/>
    </svg>
    <div class="banner__photo" role="img" aria-label="Foto eines lachenden Tanzpaares in Salsa-Haltung, Frau mit fliegenden blonden Haaren und weißem Top, Mann in grünem T-Shirt"></div>
    <div class="brand">
      <div class="brand__text">
        <span class="brand__name">Ritmo del Faro</span>
        <span class="brand__styles">Salsa · Bachata · Kizomba</span>
      </div>
      <span class="brand__dot"></span>
    </div>
    <h2 class="headline">Tanzschule</h2>
    <p class="styles">Salsa · Bachata<br>Kizomba · Zouk</p>
    <div class="offer offer--ringed">
      <span class="offer__lead">Jetzt</span>
      <span class="offer__main">GRATIS</span>
      <span class="offer__tail">Schnuppern!</span>
    </div>
    <div class="web">
      <svg class="web__icon" viewBox="0 0 16 16" aria-hidden="true" fill="none" stroke="#fff" stroke-width="1.4">
        <circle cx="8" cy="8" r="6.5"/><ellipse cx="8" cy="8" rx="3" ry="6.5"/><line x1="1.5" y1="8" x2="14.5" y2="8"/>
      </svg>
      <span>www.ritmo-del-faro.de</span>
    </div>
  </section>

</body>
</html>
```